Larkspur Talent IT Recruiting firm needs a business card design for Recruiters, Sourcers, and Account

We need business cards that allow us to change all contact info, names, titles (Recruiter, Sourcer, Account Manager, Director, CEO, etc) per person since we have three offices, in three cities, Phoenix, Austin, and Las Vegas. We do recruiting and contractors for IT positions (Developers, Architects, Software Engineers, Security Engineers, Help Desk, DBAs, PMs, Scrum Masters, etc.) Our client companies are very diverse from Meridian 100 to silicone Valley type start-ups.

So, while we what hip, techie, and quirky, it still needs to be professional. Primary color we use is blue, with silver as a secondary color.

Target Market(s)

IT, Technology

Industry/Entity Type

Business

Contact Information for Business Card

Company name: Larkspur Talent, Inc.
Website: www.larkspurtalent.example
Logos for Careerloop, Blipster, and Myriada

Name, Title, Office Number, Cell Number, email

Font styles to use
Serif
Sans Serif

Colors
0455a3
d5d5d5

Requirements
Nice to have
• The grey I selected below is not necessary - but, would like silver included. I included a card design (File 3: LTI early trial example.jpg) that I had started on. It's very rough, and not quite what we're looking for, but what we did like is the logo, big, maybe a bit faded, off center, goes out of frame, etc. Still looking for other ideas - you are the pros! But, just an idea of a design element we liked.

```html
<!DOCTYPE html>
<html lang="en">
<head>
<meta charset="utf-8">
<title>Larkspur Talent — Business Card</title>
<link rel="stylesheet" href="https://fonts.googleapis.com/css2?family=Marcellus&family=Cinzel:wght@400&family=Open+Sans:wght@400;700;800&display=swap">
<style>
  :root {
    --brand-blue: #0455a3;
    --band-blue: #1a82b0;
    --band-blue-dark: #0f6a95;
    --sky-blue: #3aa3d6;
    --ink: #2a2a2a;
    --muted: #7b8086;
    --silver: #d5d5d5;
    --card-white: #fbfbfc;
    --card-silver: #e3e5e8;
    --ghost: #cfe0ec;
    --backdrop: #eeeeee;
  }
  * { box-sizing: border-box; margin: 0; padding: 0; }
  html, body { width: 1200px; height: 1023px; overflow: hidden; }
  body {
    background: var(--backdrop);
    display: flex;
    align-items: center;
    justify-content: center;
    gap: 40px;
    font-family: "Open Sans", sans-serif;
  }
  .card {
    position: relative;
    width: 540px;
    height: 309px;
    overflow: hidden;
    border-radius: 3px;
    background: linear-gradient(135deg, var(--card-white) 0%, var(--card-silver) 100%);
    box-shadow: 0 2px 10px rgba(0,0,0,.12);
  }

  .ghost-mark {
    position: absolute;
    border-radius: 50%;
    background: radial-gradient(circle at 40% 40%, var(--ghost) 0%, rgba(207,224,236,.55) 55%, rgba(207,224,236,0) 72%);
  }
  .card-front .ghost-mark { width: 320px; height: 320px; right: -90px; top: -60px; }
  .card-back .ghost-mark { width: 360px; height: 360px; left: 60px; bottom: -190px; }

  .band {
    position: absolute; left: 0; top: 0; bottom: 0; width: 150px;
    background: linear-gradient(180deg, var(--sky-blue) 0%, var(--band-blue) 55%, var(--band-blue-dark) 100%);
    border-right: 6px solid #fff;
    box-shadow: 2px 0 0 var(--band-blue);
  }
  .band-mark {
    position: absolute; left: 35px; top: 30px;
    width: 74px; height: 74px; border-radius: 50%;
    background: #fff;
    border: 5px solid var(--silver);
  }
  .band-company {
    position: absolute; left: 0; right: 0; bottom: 24px;
    color: #fff; font-weight: 800; font-size: 10.5px; letter-spacing: .3px;
    text-align: center; text-transform: uppercase; white-space: nowrap;
  }

  .wordmark {
    font-family: "Marcellus", serif;
    color: var(--ink);
    text-transform: uppercase;
    line-height: 1;
    white-space: nowrap;
  }
  .wordmark .dot {
    display: inline-block; border-radius: 50%;
    background: var(--sky-blue); vertical-align: middle;
  }
  .tagline {
    font-family: "Cinzel", serif; color: var(--muted);
    text-transform: uppercase; letter-spacing: 1.5px; white-space: nowrap;
  }

  .front-body { position: absolute; left: 176px; top: 24px; right: 20px; }
  .front-body .wordmark { font-size: 30px; letter-spacing: 1px; }
  .front-body .wordmark .dot { width: 14px; height: 14px; margin-right: 8px; margin-top: -4px; }
  .front-body .tagline { font-size: 9px; margin-top: 6px; }
  .person-name { font-weight: 700; font-size: 21px; color: #3b3b3b; margin-top: 14px; }
  .person-title { font-size: 12px; color: var(--muted); margin-top: 1px; }

  .contact-list { list-style: none; margin-top: 10px; }
  .contact-list li {
    display: flex; align-items: center; gap: 8px;
    font-size: 12.5px; color: var(--band-blue); line-height: 19px; white-space: nowrap;
  }
  .contact-icon {
    width: 12px; height: 12px; flex: none; border-radius: 2px;
    background: #6d7378;
  }
  .contact-icon svg { display: block; width: 12px; height: 12px; }

  .back-body { position: absolute; left: 44px; top: 44px; }
  .back-body .wordmark { font-size: 44px; letter-spacing: 2px; }
  .back-body .wordmark .dot { width: 20px; height: 20px; margin-right: 10px; margin-top: -6px; }
  .back-body .tagline { font-size: 12px; margin-top: 10px; }
  .back-company {
    margin-top: 8px; font-weight: 800; font-size: 24px;
    color: var(--brand-blue); text-transform: uppercase; white-space: nowrap;
  }
</style>
</head>
<body>

  <section class="card card-front" aria-label="Business card front">
    <div class="ghost-mark" role="img" aria-label="Large faded brand symbol decoration"></div>
    <div class="band">
      <div class="band-mark"></div>
      <div class="band-company">Larkspur Talent, Inc</div>
    </div>
    <div class="front-body">
      <div class="wordmark"><span class="dot"></span>Larkspur Talent</div>
      <div class="tagline">Talent meets tomorrow</div>
      <div class="person-name">Dana Whitlock</div>
      <div class="person-title">Manager</div>
      <ul class="contact-list">
        <li><span class="contact-icon"><svg viewBox="0 0 12 12"><path d="M3.5 2.5l1.5 2-1 1c.5 1 1.5 2 2.5 2.5l1-1 2 1.5-1 1.5C5.5 10 2 6.5 2 3.5z" fill="#fff"/></svg></span>00 4510-2291</li>
        <li><span class="contact-icon"><svg viewBox="0 0 12 12"><rect x="4" y="2" width="4" height="8" rx="1" fill="none" stroke="#fff"/></svg></span>03 417 550 218</li>
        <li><span class="contact-icon"></span>www.blipster.example</li>
        <li><span class="contact-icon"></span>www.myriada.example</li>
        <li><span class="contact-icon"><svg viewBox="0 0 12 12"><rect x="2" y="3.5" width="8" height="5" fill="none" stroke="#fff"/><path d="M2 3.5l4 3 4-3" fill="none" stroke="#fff"/></svg></span>dwhitlock@mailnest.example</li>
        <li><span class="contact-icon"><svg viewBox="0 0 12 12"><circle cx="6" cy="6" r="3.5" fill="none" stroke="#fff"/><path d="M2.5 6h7M6 2.5v7" stroke="#fff"/></svg></span>www.larkspurtalent.example</li>
      </ul>
    </div>
  </section>

  <section class="card card-back" aria-label="Business card back">
    <div class="ghost-mark" role="img" aria-label="Large faded brand symbol decoration"></div>
    <div class="back-body">
      <div class="wordmark"><span class="dot"></span>Larkspur Talent</div>
      <div class="tagline">Talent meets tomorrow</div>
      <div class="back-company">Larkspur Talent, Inc</div>
    </div>
  </section>

</body>
</html>
```